Business Card Design (NEW FILES)

ATTENTION: New vector files are available. Please update your design to reflect/use the new (better resolution) logo images.

Seeking a unique and professional business card design for a commercial drone photography/videography business. The layout should feature
the logo (attached) and include the following information:
Owen Tarrick
614-502-7738
www.skylarkreelworks.example
NRD Certified Remote Pilot

Owen Tarrick

```html
<!DOCTYPE html>
<html lang="en">
<head>
<meta charset="utf-8">
<title>Skylark Reelworks – Business Card</title>
<link href="https://fonts.googleapis.com/css2?family=Montserrat:wght@400;500&family=Open+Sans:wght@400;600;700;800&display=swap" rel="stylesheet">
<style>
  :root {
    --backdrop: #232323;
    --navy: #171c4d;
    --navy-deep: #111540;
    --navy-band: #1b2158;
    --emboss: #26307a;
    --emboss-light: #2e3a90;
    --orange: #f0873f;
    --white: #ffffff;
  }
  * { box-sizing: border-box; margin: 0; padding: 0; }
  html, body { width: 1200px; height: 780px; overflow: hidden; }
  body {
    background: var(--backdrop);
    font-family: "Open Sans", Arial, sans-serif;
    position: relative;
  }
  .card {
    position: absolute;
    top: 75px;
    width: 360px;
    height: 630px;
    border-radius: 22px;
    background: var(--navy);
    overflow: hidden;
    box-shadow: 0 18px 40px rgba(0,0,0,.55);
  }
  .card--back { left: 200px; }
  .card--front { left: 640px; }

  /* Back */
  .back-mark {
    position: absolute;
    left: 50%; top: 50%;
    width: 520px;
    transform: translate(-50%, -50%) rotate(-90deg);
    text-align: center;
  }
  .back-mark__dot {
    display: inline-block;
    width: 46px; height: 46px;
    border-radius: 50%;
    background: var(--emboss-light);
    vertical-align: middle;
    margin-right: 14px;
  }
  .back-mark__name {
    font-family: "Montserrat", Arial, sans-serif;
    font-weight: 400;
    font-size: 44px;
    letter-spacing: 2px;
    color: var(--emboss);
    vertical-align: middle;
    text-transform: uppercase;
    text-shadow: none;
  }

  /* Front */
  .front-bands { position: absolute; inset: 0; }
  .brand {
    position: absolute;
    top: 90px; left: 0; right: 0;
    text-align: center;
  }
  .brand__dot {
    display: inline-block;
    width: 22px; height: 22px;
    border-radius: 50%;
    background: var(--orange);
    vertical-align: middle;
    margin-right: 8px;
  }
  .brand__name {
    font-family: "Montserrat", Arial, sans-serif;
    font-weight: 400;
    font-size: 26px;
    letter-spacing: 1px;
    color: var(--white);
    text-transform: uppercase;
    vertical-align: middle;
  }
  .person {
    position: absolute;
    top: 250px; left: 0; right: 0;
    text-align: center;
  }
  .person__name { font-size: 30px; font-weight: 800; line-height: 1.1; }
  .person__first { color: var(--orange); }
  .person__last { color: var(--white); }
  .person__role { color: var(--white); font-size: 15px; font-weight: 600; margin-top: 2px; }
  .icons {
    display: flex; justify-content: center; gap: 10px;
    margin-top: 16px;
  }
  .icon {
    width: 26px; height: 26px; border-radius: 50%;
    background: var(--orange);
    display: flex; align-items: center; justify-content: center;
  }
  .contacts {
    list-style: none;
    margin-top: 12px;
    color: var(--white);
    font-size: 14px;
    font-weight: 600;
    line-height: 1.45;
  }
  .credentials {
    position: absolute;
    bottom: 70px; left: 0; right: 0;
    text-align: center;
    color: var(--white);
    font-size: 15px;
    font-weight: 600;
    line-height: 1.4;
  }
</style>
</head>
<body>

  <section class="card card--back" aria-label="Card back">
    <div class="back-mark">
      <span class="back-mark__dot"></span><span class="back-mark__name">Skylark Reelworks</span>
    </div>
  </section>

  <section class="card card--front" aria-label="Card front">
    <svg class="front-bands" width="360" height="630" viewBox="0 0 360 630" aria-hidden="true">
      <path d="M0 300 C40 420 130 480 250 470 C300 466 340 445 360 420 L360 630 L0 630 Z" fill="var(--navy-deep)"/>
      <path d="M0 500 C80 470 180 470 260 470 C300 468 335 455 360 440 L360 630 L0 630 Z" fill="var(--navy-band)"/>
      <path d="M60 630 C120 560 200 500 300 470 L360 455 L360 630 Z" fill="var(--navy)"/>
    </svg>

    <div class="brand">
      <span class="brand__dot"></span><span class="brand__name">Skylark Reelworks</span>
    </div>

    <div class="person">
      <p class="person__name"><span class="person__first">Owen</span> <span class="person__last">Tarrick</span></p>
      <p class="person__role">Owner</p>
      <div class="icons">
        <span class="icon" aria-label="Phone">
          <svg width="14" height="14" viewBox="0 0 24 24"><path d="M6.6 10.8a15 15 0 0 0 6.6 6.6l2.2-2.2a1 1 0 0 1 1-.25 11.4 11.4 0 0 0 3.6.6 1 1 0 0 1 1 1V20a1 1 0 0 1-1 1A17 17 0 0 1 3 4a1 1 0 0 1 1-1h3.5a1 1 0 0 1 1 1c0 1.25.2 2.45.6 3.6a1 1 0 0 1-.25 1z" fill="#fff"/></svg>
        </span>
        <span class="icon" aria-label="Email">
          <svg width="14" height="14" viewBox="0 0 24 24"><rect x="3" y="6" width="18" height="12" rx="1.5" fill="none" stroke="#fff" stroke-width="2"/><path d="M3 7l9 6 9-6" fill="none" stroke="#fff" stroke-width="2"/></svg>
        </span>
        <span class="icon" aria-label="Website">
          <svg width="14" height="14" viewBox="0 0 24 24"><circle cx="12" cy="12" r="9" fill="none" stroke="#fff" stroke-width="2"/><path d="M3 12h18M12 3c3 3 3 15 0 18M12 3c-3 3-3 15 0 18" fill="none" stroke="#fff" stroke-width="1.6"/></svg>
        </span>
      </div>
      <ul class="contacts">
        <li>614-502-7738</li>
        <li>www.skylarkreelworks.example</li>
        <li>info@skylarkreelworks.example</li>
      </ul>
    </div>

    <div class="credentials">
      <p>NRD Certified Remote Pilot</p>
      <p>Fully Insured</p>
    </div>
  </section>

</body>
</html>
```